Wed site for biomedical device startup

We need a generic website for a medical device startup. I will provide examples below of websites from other companies that can serve as models for what we are looking for. The startup is for a device that can non invasively measure blood flow in the brain using light. The application is to detect the type of stroke someone is having before they get to the hospital so treatment can be started right away. This saves patients upto hours of delayed treatment. Patients will be able to recover from stroke much better and faster as a result. I have attached an AI generated illustration of what the device will ultimately look like for reference.

https://www.372clinicaltech.com
https://vextalune.com

Target Market(s)

Biomedical, medical device, investors of biomedical device startups

Industry/Entity Type

Biomedical

Coding

Coded - Design and coding required

Number of Pages Required

4 page

Requirements
Must have
• same section and section headings as example websites listed above
Nice to have
• similar to example websites listed above. Prefer a darker website over a lighter one. Perhaps dark blues to go with logo colors. A moving background image element at top of landing page could be cool. Something indicative of heartbeat, or neurons, or blood flow.

```html
<!DOCTYPE html>
<html lang="en">
<head>
<meta charset="utf-8">
<title>Lumora – Biomedical Innovation</title>
<link href="https://fonts.googleapis.com/css2?family=Montserrat:wght@300;400;500;600;700;800&display=swap" rel="stylesheet">
<style>
:root{
  --navy:#0c0a48;
  --navy-deep:#07062e;
  --ink:#1a1a2e;
  --cyan:#1ec6e8;
  --purple:#8b2fe0;
  --violet:#6a2bd9;
  --muted:#4a4a5a;
  --soft:#efeff7;
  --white:#ffffff;
  --grad:linear-gradient(90deg,var(--cyan),var(--purple));
  --grad-v:linear-gradient(180deg,#8a3ce8 0%,#5a6be6 55%,#1ec8e6 100%);
}
*{box-sizing:border-box;margin:0;padding:0}
html,body{width:1200px;height:4248px;overflow:hidden}
body{font-family:'Montserrat',sans-serif;color:var(--ink);background:var(--white);position:relative}
a{color:inherit;text-decoration:none}

/* header */
.site-header{position:absolute;left:0;top:0;width:1200px;height:92px;background:var(--white)}
.brand{position:absolute;display:flex;align-items:center;gap:12px;font-weight:500;letter-spacing:1px}
.brand .dot{width:40px;height:40px;border-radius:50%;background:var(--violet)}
.site-header .brand{left:118px;top:24px;font-size:32px;color:var(--navy)}
.main-nav a{position:absolute;top:35px;font-size:14px;font-weight:500;color:var(--ink)}
.main-nav a.active{color:var(--cyan)}
.btn-outline-dark{position:absolute;left:786px;top:20px;width:140px;height:48px;border:2px solid var(--violet);border-radius:3px;display:flex;align-items:center;justify-content:center;font-size:14px;font-weight:700;color:var(--navy);letter-spacing:.5px}
.phone-block{position:absolute;left:961px;top:0;width:239px;height:92px;background:var(--navy-deep);display:flex;align-items:center;padding-left:22px;gap:14px;color:var(--white)}
.phone-ring{width:38px;height:38px;border:1.5px solid var(--cyan);border-radius:50%;display:flex;align-items:center;justify-content:center}
.phone-label{font-size:10px;letter-spacing:2px;font-weight:500}
.phone-num{font-size:20px;font-weight:800;margin-top:2px}

/* hero */
.hero{position:absolute;left:0;top:92px;width:1200px;height:594px;background:radial-gradient(ellipse at 78% 50%,#0b1e5c 0%,#050a26 45%,#01020a 100%)}
.hero-visual{position:absolute;left:600px;top:0;width:600px;height:594px;background:radial-gradient(ellipse at 55% 50%,rgba(120,170,255,.55) 0%,rgba(40,80,200,.3) 30%,rgba(5,10,40,0) 65%)}
.hero h1{position:absolute;left:119px;top:112px;font-size:40px;line-height:48px;color:var(--white);font-weight:300}
.hero h1 .c{color:var(--cyan);font-weight:800;display:block}
.hero h1 .p{color:var(--purple);font-weight:800;display:block}
.hero-lead{position:absolute;left:119px;top:272px;width:410px;font-size:19px;line-height:30px;font-weight:500;color:var(--white);letter-spacing:-.2px}
.btn-grad{position:absolute;background:var(--grad);color:var(--white);font-weight:700;display:flex;align-items:center;justify-content:center;letter-spacing:.3px}
.hero .btn-grad{left:119px;top:384px;width:217px;height:46px;font-size:14px}
.dots{position:absolute;left:119px;top:510px;display:flex;gap:10px}
.dots span{width:13px;height:13px;border-radius:50%;border:1.5px solid #bbb}
.dots span.on{background:var(--cyan);border-color:var(--cyan)}

/* about */
.about{position:absolute;left:0;top:686px;width:1200px;height:501px;background:var(--navy)}
.about-photo{position:absolute;left:0;top:0;width:554px;height:501px;background:linear-gradient(135deg,#e8d6cc 0%,#c9a690 45%,#3b3f4a 100%)}
.sec-title{font-size:34px;font-weight:300}
.sec-title b{font-weight:800}
.about h2{position:absolute;left:606px;top:84px;color:var(--white)}
.about h2 b{color:var(--cyan)}
.about p{position:absolute;left:606px;top:161px;width:480px;font-size:15.5px;line-height:27.5px;color:var(--white);text-align:justify}
.btn-line{position:absolute;border:2px solid var(--violet);border-radius:3px;color:var(--white);font-size:14px;font-weight:700;display:flex;align-items:center;justify-content:center}
.about .btn-line{left:606px;top:356px;width:172px;height:46px}

/* technology */
.tech{position:absolute;left:0;top:1187px;width:1200px;height:547px;background:var(--soft)}
.tech h2{position:absolute;left:0;width:1200px;top:88px;text-align:center}
.rule{position:absolute;height:2px;background:var(--grad)}
.tech .rule{left:540px;top:145px;width:120px}
.tech p{position:absolute;left:150px;width:900px;top:176px;text-align:center;font-size:16px;line-height:28px;color:var(--ink)}
.tech-card{position:absolute;top:268px;width:218px;height:170px;border-radius:14px;background:var(--grad-v);box-shadow:0 10px 22px rgba(60,40,140,.25);color:var(--white);text-align:center}
.tech-card svg{position:absolute;left:79px;top:24px}
.tech-card span{position:absolute;left:0;width:100%;top:102px;font-size:17px;font-weight:700;line-height:22px}

/* pipeline */
.pipeline{position:absolute;left:0;top:1734px;width:1200px;height:611px;background:var(--white)}
.pipeline h2{position:absolute;right:633px;top:112px;color:var(--ink)}
.pipe-line{position:absolute;left:559px;top:220px;width:2px;height:182px;background:var(--violet)}
.pipe-item{position:absolute;right:656px;width:520px;text-align:right}
.pipe-item h3{font-size:19px;font-weight:700;color:var(--purple);letter-spacing:.2px}
.pipe-item p{font-size:13px;line-height:19px;color:var(--muted);margin-top:6px}
.pipe-dot{position:absolute;left:555px;width:10px;height:10px;border-radius:50%;background:var(--navy)}
.ring{position:absolute;border-radius:50%}
.pipe-photo{position:absolute;left:687px;top:138px;width:336px;height:336px;border-radius:50%;background:linear-gradient(135deg,#cfd6e2 0%,#e6e2dd 50%,#6a7382 100%)}

/* news */
.news{position:absolute;left:0;top:2345px;width:1200px;height:794px;background:radial-gradient(ellipse at 50% 30%,#16186a 0%,#0a0c48 55%,#060834 100%)}
.news h2{position:absolute;left:0;width:1200px;top:100px;text-align:center;color:var(--white)}
.news .rule{left:540px;top:160px;width:120px}
.news-card{position:absolute;top:208px;width:308px;height:420px;color:var(--white)}
.news-card .img{width:308px;height:229px}
.news-card .edge{position:absolute;right:0;top:270px;width:2px;height:100px;background:linear-gradient(180deg,var(--cyan),var(--violet))}
.news-card h3{margin-top:20px;font-size:18px;line-height:22px;font-weight:700;width:290px}
.news-card p{margin-top:22px;font-size:11px;line-height:16px;width:290px}
.news-card .more{margin-top:18px;display:flex;align-items:center;gap:8px;font-size:14px;font-weight:600}
.news .btn-line{left:514px;top:658px;width:172px;height:46px}

/* contact */
.contact{position:absolute;left:0;top:3139px;width:1200px;height:701px;background:var(--white)}
.contact-photo{position:absolute;left:0;top:0;width:560px;height:701px;background:linear-gradient(90deg,#3d5870 0%,#8fa6ba 55%,#e8eef4 100%)}
.contact h2{position:absolute;left:560px;top:100px;color:var(--ink)}
.contact .rule{left:560px;top:148px;width:114px}
.contact .intro{position:absolute;left:560px;top:178px;width:460px;font-size:14.5px;line-height:23px;color:var(--muted)}
.field{position:absolute;left:560px;width:528px;height:41px;border:1px solid #d4d4dc;border-radius:3px;display:flex;align-items:center;padding-left:12px;gap:14px;font-size:13.5px;color:#444;background:var(--white)}
.field.msg{height:122px;align-items:flex-start;padding-top:12px}
.contact .btn-grad{left:560px;top:567px;width:173px;height:47px;font-size:14px}

/* footer */
.site-footer{position:absolute;left:0;top:3840px;width:1200px;height:408px;background:radial-gradient(ellipse at 50% 20%,#14176a 0%,#0a0c4a 60%,#07083a 100%);color:var(--white)}
.site-footer .brand{left:185px;top:112px;font-size:34px;color:var(--white)}
.social{position:absolute;top:201px;width:36px;height:36px;border-radius:50%;border:1.5px solid var(--white)}
.social.on{background:var(--violet);border-color:var(--violet)}
.foot-col{position:absolute;top:72px}
.foot-col h4{font-size:19px;font-weight:700}
.foot-col .bar{width:62px;height:2px;background:var(--grad);margin-top:10px;margin-bottom:14px}
.foot-col a{display:block;font-size:12.5px;line-height:26px}
.foot-rule{position:absolute;left:112px;top:302px;width:976px;height:1px;background:rgba(255,255,255,.25)}
.copy{position:absolute;left:0;width:1200px;top:341px;text-align:center;font-size:13.5px}
.copy a{color:var(--cyan);text-decoration:underline}
.to-top{position:absolute;left:1127px;top:283px;width:41px;height:40px;border-radius:6px;background:linear-gradient(135deg,var(--cyan),var(--purple));display:flex;align-items:center;justify-content:center}
</style>
</head>
<body>

<header class="site-header">
  <div class="brand"><span class="dot"></span>Lumora</div>
  <nav class="main-nav">
    <a class="active" style="left:476px">Home</a>
    <a style="left:547px">About</a>
    <a style="left:618px">Technology</a>
    <a style="left:723px">Press</a>
  </nav>
  <a class="btn-outline-dark">CONTACT US</a>
  <div class="phone-block">
    <div class="phone-ring">
      <svg width="18" height="18" viewBox="0 0 24 24" fill="none" stroke="#1ec6e8" stroke-width="2"><path d="M5 3h4l2 5-2.5 1.5a11 11 0 0 0 6 6L16 13l5 2v4a2 2 0 0 1-2 2A17 17 0 0 1 3 5a2 2 0 0 1 2-2z"/></svg>
    </div>
    <div><div class="phone-label">TALK TO AN AGENT</div><div class="phone-num">555.014.2290</div></div>
  </div>
</header>

<section class="hero">
  <div class="hero-visual" role="img" aria-label="Glowing blue neuron network illustration"></div>
  <h1>Engineering Tomorrow's<span class="c">Biomedical</span><span class="p">Breakthroughs</span></h1>
  <p class="hero-lead">Innovative technologies transforming<br>diagnostics and treatment in critical care<br>and beyond.</p>
  <a class="btn-grad">EXPLORE OUR PIPELINE</a>
  <div class="dots"><span></span><span></span><span class="on"></span></div>
</section>

<section class="about">
  <div class="about-photo" role="img" aria-label="Patient wearing forehead sensor pads beside a handheld monitor"></div>
  <h2 class="sec-title">About <b>Our Company</b></h2>
  <p>We are a biomedical innovation company focused on developing transformative solutions for high-acuity and underserved conditions. Our team brings together leading researchers, engineers, and medical professionals with a shared mission: to push the boundaries of what's possible in modern healthcare.</p>
  <a class="btn-line">LEARN MORE</a>
</section>

<section class="tech">
  <h2 class="sec-title">Our <b>Technology</b></h2>
  <div class="rule"></div>
  <p>Our proprietary platform leverages real-time biosignal analytics, advanced sensor integration, and adaptive AI models to enable earlier detection, faster intervention, and better patient outcomes.</p>
  <div class="tech-card" style="left:181px">
    <svg width="60" height="60" viewBox="0 0 60 60" fill="none" stroke="#fff" stroke-width="2"><rect x="5" y="6" width="50" height="36" rx="2"/><path d="M24 42v8h12v-8M18 52h24M11 14h12M11 20h12M11 26h8M12 34l6 0 3-5 4 8 3-4h6"/><rect x="34" y="20" width="3" height="8"/><rect x="40" y="16" width="3" height="12"/><rect x="46" y="22" width="3" height="6"/></svg>
    <span>Smart monitoring<br>tools</span>
  </div>
  <div class="tech-card" style="left:489px">
    <svg width="60" height="60" viewBox="0 0 60 60" fill="none" stroke="#fff" stroke-width="2"><circle cx="25" cy="25" r="17"/><path d="M37 37l14 14M14 26h5l3-6 5 12 3-6h6"/><circle cx="44" cy="12" r="4"/><path d="M44 4v3M44 17v3M36 12h3M49 12h3"/></svg>
    <span>AI-enhanced<br>diagnostics</span>
  </div>
  <div class="tech-card" style="left:799px">
    <svg width="60" height="60" viewBox="0 0 60 60" fill="none" stroke="#fff" stroke-width="2"><circle cx="18" cy="16" r="10"/><path d="M18 6v10h10M34 10h18M34 16h14M34 22h18M6 52h48"/><rect x="10" y="38" width="6" height="14"/><rect x="22" y="32" width="6" height="20"/><rect x="34" y="40" width="6" height="12"/><rect x="46" y="30" width="6" height="22"/></svg>
    <span>Data-driven<br>decision support</span>
  </div>
</section>

<section class="pipeline">
  <h2 class="sec-title">Our <b>Pipeline</b></h2>
  <div class="pipe-line"></div>
  <div class="pipe-dot" style="top:214px"></div>
  <div class="pipe-dot" style="top:304px"></div>
  <div class="pipe-dot" style="top:395px"></div>
  <div class="pipe-item" style="top:207px"><h3>PROGRAM A – EARLY DETECTION PLATFORM</h3><p>Non-invasive, real-time biosignal analysis for early-stage interventions in<br>cardiovascular events.</p></div>
  <div class="pipe-item" style="top:297px"><h3>PROGRAM B – PULSEMAP</h3><p>Smart neuro-diagnostics leveraging adaptive algorithms<br>for fast, accurate screening of neurological disorders.</p></div>
  <div class="pipe-item" style="top:388px"><h3>PROGRAM C – VASCULYTE</h3><p>Advanced blood-flow analytics and visualization for<br>trauma and surgical applications.</p></div>
  <div class="ring" style="left:596px;top:47px;width:518px;height:518px;border:1px solid #e3e8f4"></div>
  <div class="ring" style="left:624px;top:75px;width:462px;height:462px;border:2px solid #9ad6f0"></div>
  <div class="ring" style="left:657px;top:108px;width:396px;height:396px;border:3px solid var(--violet)"></div>
  <div class="pipe-photo" role="img" aria-label="Child wearing an EEG electrode cap"></div>
</section>

<section class="news">
  <h2 class="sec-title">Latest <b>News</b></h2>
  <div class="rule"></div>
  <article class="news-card" style="left:99px">
    <div class="img" role="img" aria-label="Man lying down with EEG electrodes attached" style="background:linear-gradient(135deg,#d7e4ee,#b9c8d6 60%,#8aa0b6)"></div>
    <div class="edge"></div>
    <h3>Caatus error sit voluptatem accusantium doloremque laudantium</h3>
    <p>Gerspiciatis unde omnis iste natus error sit voluptatem accusantium doloremque laudantium.</p>
    <a class="more">Learn More <svg width="40" height="26" viewBox="0 0 40 26" fill="none" stroke="#1ec6e8" stroke-width="1.6"><circle cx="27" cy="13" r="12"/><path d="M2 13h30M26 7l6 6-6 6"/></svg></a>
  </article>
  <article class="news-card" style="left:445px">
    <div class="img" role="img" aria-label="Face with glowing digital sensor points" style="background:linear-gradient(135deg,#1c3a58,#3d6a8e 50%,#0f2236)"></div>
    <div class="edge"></div>
    <h3>Caatus error sit voluptatem accusantium doloremque laudantium</h3>
    <p>Gerspiciatis unde omnis iste natus error sit voluptatem accusantium doloremque laudantium.</p>
    <a class="more">Learn More <svg width="40" height="26" viewBox="0 0 40 26" fill="none" stroke="#1ec6e8" stroke-width="1.6"><circle cx="27" cy="13" r="12"/><path d="M2 13h30M26 7l6 6-6 6"/></svg></a>
  </article>
  <article class="news-card" style="left:791px">
    <div class="img" role="img" aria-label="Woman with EEG cap beside recording equipment" style="background:linear-gradient(135deg,#f1f2f4,#dfe2e6 60%,#c6b8a8)"></div>
    <div class="edge"></div>
    <h3>Caatus error sit voluptatem accusantium doloremque laudantium</h3>
    <p>Gerspiciatis unde omnis iste natus error sit voluptatem accusantium doloremque laudantium.</p>
    <a class="more">Learn More <svg width="40" height="26" viewBox="0 0 40 26" fill="none" stroke="#1ec6e8" stroke-width="1.6"><circle cx="27" cy="13" r="12"/><path d="M2 13h30M26 7l6 6-6 6"/></svg></a>
  </article>
  <a class="btn-line">VIEW ALL NEWS</a>
</section>

<section class="contact">
  <div class="contact-photo" role="img" aria-label="Man wearing a colourful EEG electrode cap"></div>
  <h2 class="sec-title">Contact <b>Us</b></h2>
  <div class="rule"></div>
  <p class="intro">We welcome conversations with potential partners, investors, and collaborators.</p>
  <div class="field" style="top:230px"><svg width="14" height="14" viewBox="0 0 24 24" fill="#6a2bd9"><circle cx="12" cy="7" r="5"/><path d="M3 23c0-6 4-9 9-9s9 3 9 9z"/></svg>Your Name</div>
  <div class="field" style="top:291px"><svg width="16" height="14" viewBox="0 0 24 18" fill="none" stroke="#6a2bd9" stroke-width="2.4"><rect x="1" y="1" width="22" height="16" rx="2"/><path d="M1 2l11 8 11-8"/></svg>Email</div>
  <div class="field" style="top:350px"><svg width="14" height="14" viewBox="0 0 24 24" fill="#6a2bd9"><path d="M5 2h4l2 6-3 2a12 12 0 0 0 6 6l2-3 6 2v4a3 3 0 0 1-3 3A19 19 0 0 1 2 5a3 3 0 0 1 3-3z"/></svg>Phone Number</div>
  <div class="field msg" style="top:411px"><svg width="16" height="14" viewBox="0 0 24 20" fill="#6a2bd9"><path d="M2 2h14v10H7l-4 3v-3H2z"/><path d="M18 6h4v10h-1v3l-4-3h-7v-2h8z"/></svg>Write &nbsp;A Message</div>
  <a class="btn-grad">SEND MESSAGE</a>
</section>

<footer class="site-footer">
  <div class="brand"><span class="dot"></span>Lumora</div>
  <a class="social" style="left:193px" aria-label="Social profile one"></a>
  <a class="social on" style="left:247px" aria-label="Social profile two"></a>
  <a class="social" style="left:302px" aria-label="Social profile three"></a>
  <div class="foot-col" style="left:498px"><h4>Quick links</h4><div class="bar"></div><a>Home</a><a>About</a><a>Technology</a><a>Press</a><a>Contact Us</a></div>
  <div class="foot-col" style="left:714px"><h4>Links</h4><div class="bar"></div><a>Copyright</a><a>Legal</a><a>Privacy</a><a>Accessibility</a><a>Sitemap</a></div>
  <div class="foot-col" style="left:880px"><h4>Support</h4><div class="bar"></div><a>Team</a><a>About Us</a><a>Careers</a><a>Our Values</a></div>
  <div class="foot-rule"></div>
  <a class="to-top" aria-label="Back to top"><svg width="14" height="10" viewBox="0 0 14 10" fill="none" stroke="#fff" stroke-width="2"><path d="M2 8l5-5 5 5"/></svg></a>
  <p class="copy">Copyright © 2025 <a>Biomedical Startup</a>. All rights reserved.</p>
</footer>

</body>
</html>
```